Every Shelf Set Neatly or ESN Organized needs a business card design. ESN Organized is a professi

We need a business card design that is clean, sharp and conveys a sense of organization. I already have a logo.

Target Market(s)

Families (specifically mothers), small business owners, parents, seniors

Industry/Entity Type

Business

Contact Information for Business Card

My website is www.esnorganized-example.com and my Facebook page is http://www.sociallink-example.com/everyshelfsetneatly. The phone number is 418-552-7094 and I want to be listed as Lorna M. Pelham, Owner

Requirements
Must have
• My logo.

```html
<!DOCTYPE html>
<html lang="en">
<head>
<meta charset="UTF-8">
<title>ESN Organized – Business Card</title>
<link rel="stylesheet" href="https://fonts.googleapis.com/css2?family=Montserrat:wght@400&family=Open+Sans:wght@400;700&display=swap">
<style>
  :root {
    --page-bg: #3a3d40;
    --card-white: #ffffff;
    --brand-blue: #1b87d9;
    --brand-blue-deep: #1679c6;
    --ink-dark: #2b2b2b;
    --card-black: #0b0b0b;
    --back-text: #d9d9d9;
    --rule-light: rgba(255,255,255,0.55);
  }
  * { margin: 0; padding: 0; box-sizing: border-box; }
  html, body {
    width: 1200px; height: 950px; overflow: hidden;
    background: var(--page-bg);
  }
  .stage {
    width: 1200px; height: 950px;
    display: flex; flex-direction: column;
    align-items: center; justify-content: center; gap: 50px;
  }
  .card {
    width: 700px; height: 400px; position: relative; overflow: hidden;
    box-shadow: 0 10px 30px rgba(0,0,0,0.45);
  }

  /* Front */
  .card-front { background: var(--card-white); }
  .front-logo {
    position: absolute; left: 70px; top: 80px;
    display: flex; align-items: center; gap: 18px;
  }
  .logo-mark {
    width: 34px; height: 34px; background: var(--brand-blue);
  }
  .logo-name {
    font-family: "Montserrat", sans-serif; font-weight: 400;
    font-size: 34px; letter-spacing: 4px; color: var(--ink-dark);
    text-transform: uppercase; line-height: 1.15;
  }
  .front-band {
    position: absolute; left: 0; right: 0; bottom: 0; height: 182px;
    background: var(--brand-blue);
  }
  .contact {
    position: absolute; left: 0; right: 0; top: 24px;
    font-family: "Open Sans", sans-serif; color: #fff; text-align: center;
  }
  .contact-name { font-weight: 700; font-size: 26px; letter-spacing: 0.5px; }
  .contact-role {
    display: flex; align-items: center; justify-content: center; gap: 14px;
    font-size: 17px; margin-top: 2px;
  }
  .contact-role::before, .contact-role::after {
    content: ""; width: 150px; height: 1px; background: var(--rule-light);
  }
  .contact-line { font-size: 18px; margin-top: 8px; }
  .contact-line strong { font-weight: 700; }
  .contact-line .gap { display: inline-block; width: 18px; }
  .social {
    display: inline-flex; align-items: center; gap: 8px;
  }
  .social-mark {
    width: 16px; height: 16px; background: #fff; display: inline-block;
  }

  /* Back */
  .card-back {
    background: var(--card-black);
    display: flex; flex-direction: column; align-items: center; justify-content: center;
  }
  .back-logo { display: flex; align-items: center; gap: 18px; }
  .back-logo .logo-mark { background: var(--back-text); }
  .back-logo .logo-name { color: var(--back-text); }
  .back-web {
    margin-top: 34px;
    font-family: "Montserrat", sans-serif; font-size: 18px; letter-spacing: 3px;
    color: var(--back-text);
  }
</style>
</head>
<body>
<main class="stage">
  <section class="card card-front">
    <div class="front-logo">
      <span class="logo-mark"></span>
      <span class="logo-name">Every Shelf<br>Set Neatly</span>
    </div>
    <div class="front-band">
      <div class="contact">
        <div class="contact-name">Lorna M. Pelham</div>
        <div class="contact-role">Owner</div>
        <div class="contact-line"><strong>Phone:</strong> 418-552-7094<span class="gap"></span><strong>Web:</strong> www.esnorganized-example.com</div>
        <div class="contact-line"><span class="social"><span class="social-mark"></span>everyshelfsetneatly</span></div>
      </div>
    </div>
  </section>

  <section class="card card-back">
    <div class="back-logo">
      <span class="logo-mark"></span>
      <span class="logo-name">Every Shelf<br>Set Neatly</span>
    </div>
    <div class="back-web">esnorganized-example.com</div>
  </section>
</main>
</body>
</html>
```